2018 Desk Calendar Design with Better Spine, Better Health with Chiropractic

In conjunction with the Federation of Spinal Wellness Malaysia (FSW), we are organizing a 2018 desk calendar design. The cover page and monthly design size is 210mm (H) x 195mm (W). The will be a total of 27 designs including a cover page (front) [Sample 1], cover page (back) Malaysia National & States Holiday 2018 (https://restdaylist.example.my/2018-dates/) [Sample 2], 12 months design (front) [Sample 3 and 4], 12 months design (back) [Sample 5], Last page (2017 and 2019 calendar) [Sample 6].

Below are some recommendations for monthly back cover design. The main theme remain as Better SPINE, Better HEALTH with CHIROPRACTIC. Each month can in collaborate with of the following element:-

Suggestion 1 (Celebration of the Month)
January - New Year
February - Chinese New Year
March -
April -
May - Labour Day
June - Aidilfitri Festival
July-
August - Independent Day
September - Malaysia Day
October - World Spine Day
November - Deepavali Festival
December - Christmas

Suggestion 2 (States in Malaysia)
January - Perlis
February - Kedah
March - Penang
April - Perak
May - Selangor
June - Negeri Sembilan
July- Melaka
August - Johor
September - Pahang
October - Terengganu
November - Kelantan
December - Sabah & Sarawak

Target Market(s)

Chiropractors and Public

Industry/Entity Type

Chiropractor

Colors

Designer to choose colors to be used in the design.

Requirements
Must have
• The theme for the desk calendar design is Better Spine, Better Health with Chiropractic.
• The cover page should include 5th Anniversary element.
Nice to have
• Lunar or Islamic calendar is optional in the Gregorian calendar.
• AI Format
• Footnote of each page www.spinefsw.example.org

```html
<!DOCTYPE html>
<html lang="en">
<head>
<meta charset="utf-8">
<title>FSW 2018 Desk Calendar – April</title>
<link rel="stylesheet" href="https://fonts.googleapis.com/css2?family=Michroma&family=Libre+Baskerville:wght@700&family=Arimo&display=swap">
<style>
  :root {
    --paper: #cfd0d2;
    --ink: #111111;
    --sunday: #e8262e;
    --rule: #7b2a7e;
    --plum: #7a2472;
    --band-deep: #6e2370;
    --band-pink: #b23a9a;
    --sky-top: #c9cde6;
    --sky-mid: #6b6fc4;
    --sky-low: #3b3f9e;
    --white: #ffffff;
  }
  * { margin: 0; padding: 0; box-sizing: border-box; }
  html, body { width: 1111px; height: 1200px; overflow: hidden; background: var(--paper); }
  .page { position: relative; width: 1111px; height: 1200px; background: var(--paper); overflow: hidden; font-family: "Michroma", sans-serif; color: var(--ink); }

  .artwork { position: absolute; left: 0; top: 0; width: 1111px; height: 1200px; }

  .month-grid { position: absolute; left: 211px; top: 0; }
  .month-grid .row { position: absolute; left: 0; display: flex; }
  .month-grid .cell { width: 130px; font-size: 27px; line-height: 1; }
  .month-grid .cell.sun { color: var(--sunday); }
  .month-grid .head .cell { font-size: 26px; }
  .rule { position: absolute; left: 207px; width: 890px; height: 2px; background: var(--rule); }

  .brand { position: absolute; left: 648px; top: 606px; display: flex; align-items: center; gap: 8px; }
  .brand .dot { width: 26px; height: 26px; border-radius: 50%; background: var(--plum); }
  .brand .name { font-size: 30px; color: var(--plum); }

  .month-title { position: absolute; left: 780px; top: 598px; font-size: 60px; letter-spacing: 4px; color: var(--plum); line-height: 1; }

  .mini { position: absolute; left: 838px; top: 698px; width: 240px; }
  .mini .mini-title { position: absolute; left: 80px; top: 0; font-size: 17px; letter-spacing: 1px; }
  .mini .line { position: absolute; left: 0; display: flex; }
  .mini .d { width: 36.6px; font-size: 14px; text-align: center; }
  .mini .d.sun { color: var(--sunday); }

  .spine-fact { position: absolute; right: 193px; top: 1040px; text-align: right; font-family: "Libre Baskerville", serif; font-weight: 700; font-size: 28px; line-height: 39px; color: var(--white); }

  .footnote { position: absolute; left: 19px; top: 1170px; font-family: "Arimo", sans-serif; font-size: 17px; color: var(--ink); }
</style>
</head>
<body>
<main class="page">

  <svg class="artwork" width="1111" height="1200" viewBox="0 0 1111 1200" role="img" aria-label="Photograph of two people stretching in silhouette against a cloudy blue sky, crossed by an illustrated purple spine">
    <defs>
      <linearGradient id="sky" x1="0" y1="0" x2="0.3" y2="1">
        <stop offset="0" stop-color="var(--sky-top)"/>
        <stop offset="0.45" stop-color="var(--sky-mid)"/>
        <stop offset="1" stop-color="var(--sky-low)"/>
      </linearGradient>
      <linearGradient id="band" x1="0" y1="0" x2="1" y2="1">
        <stop offset="0" stop-color="var(--band-deep)"/>
        <stop offset="0.5" stop-color="var(--band-pink)"/>
        <stop offset="1" stop-color="var(--band-deep)"/>
      </linearGradient>
    </defs>
    <path d="M0 655 C 180 690, 380 820, 600 885 C 800 945, 980 1010, 1111 1140 L 1111 1200 L 0 1200 Z" fill="url(#sky)"/>
    <path d="M0 560 C 200 600, 380 760, 600 845 C 820 925, 1000 990, 1111 1110" fill="none" stroke="url(#band)" stroke-width="70" stroke-linecap="round" opacity="0.9"/>
  </svg>

  <section class="month-grid" aria-label="April 2018">
    <div class="row head" style="top:86px">
      <span class="cell">M</span><span class="cell">T</span><span class="cell">W</span><span class="cell">T</span><span class="cell">F</span><span class="cell">S</span><span class="cell sun">S</span>
    </div>
    <div class="row" style="top:164px">
      <span class="cell">30</span><span class="cell"></span><span class="cell"></span><span class="cell"></span><span class="cell"></span><span class="cell"></span><span class="cell sun">1</span>
    </div>
    <div class="row" style="top:258px">
      <span class="cell">2</span><span class="cell">3</span><span class="cell">4</span><span class="cell">5</span><span class="cell">6</span><span class="cell">7</span><span class="cell sun">8</span>
    </div>
    <div class="row" style="top:352px">
      <span class="cell">9</span><span class="cell">10</span><span class="cell">11</span><span class="cell">12</span><span class="cell">13</span><span class="cell">14</span><span class="cell sun">15</span>
    </div>
    <div class="row" style="top:447px">
      <span class="cell">16</span><span class="cell">17</span><span class="cell">18</span><span class="cell">19</span><span class="cell">20</span><span class="cell">21</span><span class="cell sun">22</span>
    </div>
    <div class="row" style="top:545px">
      <span class="cell">23</span><span class="cell">24</span><span class="cell">25</span><span class="cell">26</span><span class="cell">27</span><span class="cell">28</span><span class="cell sun">29</span>
    </div>
  </section>
  <div class="rule" style="top:196px"></div>
  <div class="rule" style="top:290px"></div>
  <div class="rule" style="top:385px"></div>
  <div class="rule" style="top:484px"></div>
  <div class="rule" style="top:575px"></div>

  <div class="brand"><span class="dot"></span><span class="name">FSW</span></div>
  <h1 class="month-title">APRIL</h1>

  <section class="mini" aria-label="March 2018">
    <span class="mini-title">MARCH</span>
    <div class="line" style="top:38px"><span class="d">M</span><span class="d">T</span><span class="d">W</span><span class="d">T</span><span class="d">F</span><span class="d">S</span><span class="d sun">S</span></div>
    <div class="line" style="top:62px"><span class="d"></span><span class="d"></span><span class="d"></span><span class="d">1</span><span class="d">2</span><span class="d">3</span><span class="d sun">4</span></div>
    <div class="line" style="top:92px"><span class="d">5</span><span class="d">6</span><span class="d">7</span><span class="d">8</span><span class="d">9</span><span class="d">10</span><span class="d sun">11</span></div>
    <div class="line" style="top:123px"><span class="d">12</span><span class="d">13</span><span class="d">14</span><span class="d">15</span><span class="d">16</span><span class="d">17</span><span class="d sun">18</span></div>
    <div class="line" style="top:154px"><span class="d">19</span><span class="d">20</span><span class="d">21</span><span class="d">22</span><span class="d">23</span><span class="d">24</span><span class="d sun">25</span></div>
    <div class="line" style="top:184px"><span class="d">26</span><span class="d">27</span><span class="d">28</span><span class="d">29</span><span class="d">30</span><span class="d">31</span><span class="d"></span></div>
  </section>

  <p class="spine-fact">Spine Fact:<br>The spine contains more<br>than 120 muscles.</p>

  <p class="footnote">www.spinefsw.example.org</p>
</main>
</body>
</html>
```